Mindfulness School for Children -- Business Cards

We're looking for business cards for our school directors and owners. We're a mindfulness school for children called little lanterns. Attached are our logos/icons.

```html
<!DOCTYPE html>
<html lang="en">
<head>
<meta charset="utf-8">
<title>little lanterns — business cards</title>
<link rel="stylesheet" href="https://fonts.googleapis.com/css2?family=Raleway:wght@600&family=Tinos&display=swap">
<style>
  :root {
    --backdrop: #2a2522;
    --card: #1b1b1b;
    --teal: #55a595;
    --mint: #8fcf9e;
    --sky: #7ccbe0;
    --ink-light: #e6e6e6;
  }
  * { box-sizing: border-box; margin: 0; padding: 0; }
  html, body { width: 1200px; height: 842px; overflow: hidden; }
  body {
    background: var(--backdrop);
    display: flex;
    align-items: center;
    justify-content: center;
    gap: 50px;
  }
  .card {
    position: relative;
    width: 540px;
    height: 309px;
    background: var(--card);
    box-shadow: 0 12px 30px rgba(0,0,0,0.55);
    overflow: hidden;
  }
  /* back: contact side */
  .band {
    position: absolute;
    left: 0;
    width: 100%;
    height: 12px;
    background: linear-gradient(90deg, var(--teal), var(--mint));
  }
  .band--top { top: 0; }
  .band--bottom { bottom: 36px; }
  .contact {
    position: absolute;
    top: 36px;
    left: 0;
    width: 100%;
    text-align: center;
    font-family: "Tinos", serif;
    color: var(--ink-light);
    font-size: 17px;
    line-height: 1.12;
  }
  .contact__name {
    font-family: "Raleway", sans-serif;
    font-weight: 600;
    font-size: 24px;
    line-height: 1;
  }
  .contact__first { color: var(--teal); }
  .contact__last { color: var(--sky); }
  .contact__role { font-size: 16px; margin-bottom: 6px; }
  .divider {
    width: 62px;
    height: 1px;
    background: var(--sky);
    margin: 8px auto 10px;
  }
  /* front: brand side */
  .accent {
    position: absolute;
    display: flex;
  }
  .accent__block { width: 30px; height: 38px; }
  .accent__line { width: 4px; height: 38px; background: var(--sky); }
  .accent--left { left: 0; top: 178px; }
  .accent--left .accent__block { background: var(--teal); }
  .accent--left .accent__line { margin-left: 5px; }
  .accent--right { right: 0; top: 62px; flex-direction: row-reverse; }
  .accent--right .accent__block { background: var(--mint); }
  .accent--right .accent__line { margin-right: 5px; }
  .brand {
    position: absolute;
    inset: 0;
    display: flex;
    align-items: center;
    justify-content: center;
    gap: 12px;
    font-family: "Raleway", sans-serif;
    font-weight: 600;
    font-size: 38px;
    color: var(--teal);
    letter-spacing: 0.5px;
  }
  .brand__dot {
    width: 14px;
    height: 14px;
    border-radius: 50%;
    background: var(--teal);
  }
</style>
</head>
<body>
  <section class="card card--back" aria-label="Contact side">
    <div class="band band--top"></div>
    <div class="contact">
      <p class="contact__name"><span class="contact__first">Maya</span> <span class="contact__last">Ellison</span></p>
      <p class="contact__role">Managing Director</p>
      <div class="divider"></div>
      <p>044-555 018 274</p>
      <p>hello@lanternmail.com</p>
      <p>www.littlelanterns.org</p>
      <div class="divider"></div>
      <p>421, Address line goes here</p>
      <p>45452,Country Name</p>
    </div>
    <div class="band band--bottom"></div>
  </section>

  <section class="card card--front" aria-label="Brand side">
    <div class="accent accent--right"><span class="accent__block"></span><span class="accent__line"></span></div>
    <div class="brand"><span class="brand__dot"></span><span>little lanterns</span></div>
    <div class="accent accent--left"><span class="accent__block"></span><span class="accent__line"></span></div>
  </section>
</body>
</html>
```